Business cards and stationary design

We just completed the design of our new logo and we need to print new business cards and letterhead for our nonprofit. We are looking for a fresh new design that shows off our new logo. On letterhead, we must have a column on the right or left to include our Board of Directors (up to 45 names) (see attachment)

Industry/Entity Type

Non-Profit

Contact Information for Business Card

Standard business card with name, title, Company name, mailing address phone numbers, email address and website. Tagline on back "Bringing the homeless home"

Font styles to use
Sans Serif

Requirements
Must have
• include pertinent information above
• new logo
• fonts compatible with logo
• should use logo colors only
Nice to have
• tag lines

```html
<!DOCTYPE html>
<html lang="en">
<head>
<meta charset="utf-8">
<title>Harbor Hope Center – Business Card</title>
<link rel="stylesheet" href="https://fonts.googleapis.com/css2?family=Courier+Prime:wght@400;700&family=Lato:wght@400;700&display=swap">
<style>
  :root {
    --backdrop: #9a9a9a;
    --paper: #ffffff;
    --ink-dark: #232323;
    --text-grey: #666666;
    --brand-teal: #0e7fa0;
    --brand-red: #e5161d;
    --brand-yellow: #f9b526;
    --back-text: #e8e8e8;
  }
  * { margin: 0; padding: 0; box-sizing: border-box; }
  html, body {
    width: 1200px; height: 900px; overflow: hidden;
    background: var(--backdrop);
    font-family: "Lato", Arial, sans-serif;
  }
  .stage { position: relative; width: 1200px; height: 900px; }
  .card {
    position: absolute; top: 306px; width: 439px; height: 272px;
    box-shadow: 2px 3px 5px rgba(0,0,0,0.35);
    overflow: hidden;
  }
  .card--front { left: 150px; background: var(--paper); }
  .card--back { left: 609px; background: var(--ink-dark); }

  .holder { position: absolute; left: 24px; top: 32px; }
  .holder__name {
    font-family: "Courier Prime", "Courier New", monospace;
    font-weight: 700; font-size: 15px; letter-spacing: 0.5px;
    color: var(--brand-teal);
  }
  .holder__name .surname { color: var(--brand-red); }
  .holder__title {
    margin-top: 2px; font-size: 11px; color: var(--text-grey);
    text-transform: uppercase;
  }

  .brand {
    position: absolute; display: flex; align-items: center; gap: 8px;
    font-family: "Lato", Arial, sans-serif; font-weight: 700;
    color: var(--brand-teal);
  }
  .card--front .brand { right: 24px; top: 122px; font-size: 22px; }
  .card--back .brand {
    left: 0; right: 0; justify-content: center; top: 150px;
    font-size: 26px; color: var(--brand-yellow);
  }
  .brand__mark { width: 14px; height: 14px; background: var(--brand-red); }
  .card--back .brand__mark { width: 16px; height: 16px; }

  .contact { position: absolute; left: 23px; top: 195px; list-style: none; }
  .contact li {
    display: flex; align-items: center; gap: 5px;
    font-size: 12px; color: var(--text-grey); line-height: 17px;
  }
  .contact li:first-child { font-size: 13px; }
  .contact svg { width: 10px; height: 10px; fill: var(--brand-teal); }

  .address {
    position: absolute; right: 23px; top: 213px;
    font-size: 11px; color: var(--text-grey); text-align: right;
    line-height: 15px; font-style: normal; text-transform: uppercase;
  }

  .colour-bar { position: absolute; left: 0; bottom: 0; width: 100%; height: 14px; display: flex; }
  .colour-bar span { height: 100%; }
  .colour-bar .yellow { width: 142px; background: var(--brand-yellow); }
  .colour-bar .teal { width: 148px; background: var(--brand-teal); }
  .colour-bar .red { flex: 1; background: var(--brand-red); }

  .website {
    position: absolute; left: 0; right: 0; top: 220px; text-align: center;
    font-family: "Courier Prime", "Courier New", monospace;
    font-size: 13px; letter-spacing: 0.5px; color: var(--back-text);
  }
</style>
</head>
<body>
<main class="stage">
  <section class="card card--front" aria-label="Business card front">
    <div class="holder">
      <p class="holder__name">DANIEL <span class="surname">CARTER</span></p>
      <p class="holder__title">Managing Director</p>
    </div>

    <div class="brand"><span class="brand__mark"></span>Harbor Hope Center</div>

    <ul class="contact">
      <li><svg viewBox="0 0 10 10"><path d="M1 3c0-1 1-2 4-2s4 1 4 2v1H7V3H3v1H1zM2 5h6l1 4H1z"/></svg>444 555 6688</li>
      <li><svg viewBox="0 0 10 10"><path d="M0 2h10v6H0z M0 2l5 3 5-3" stroke="#fff" stroke-width="0.8"/></svg>INFO@YOUREMAIL.COM</li>
      <li><svg viewBox="0 0 10 10"><circle cx="5" cy="5" r="4.5"/></svg>WWW.WEBSITENAME.COM</li>
    </ul>

    <address class="address">421, Address Line Here<br>Country Name,45452</address>

    <div class="colour-bar"><span class="yellow"></span><span class="teal"></span><span class="red"></span></div>
  </section>

  <section class="card card--back" aria-label="Business card back">
    <div class="brand"><span class="brand__mark"></span>Harbor Hope Center</div>
    <p class="website">WWW.WEBSITENAME.COM</p>
  </section>
</main>
</body>
</html>
```